New Business Card Design for Manufacturing

We are an engineering/manufacturing company that offers Advanced machining/assembly/engineering services, as well as innovative products for the heavy duty engine cooling markets.

We are looking to get a new business card designed that is clean and modern looking, but still fits the wide range of technical/skilled work we do.

- We hope to use this design as the base for other design work in new Presentations, web, and print work.

Industry/Entity Type

Engineering

Contact Information for Business Card

Our preferred color of blue is (RGB) 22/71/159 but can vary slightly from that color. Our content will be our Logo and full company name (Vantrell Forge Works, Inc.), company address, name, job title, phone number with extension, cell number, fax number, website, and email address on the cards.
We'd like the full company name next to the logo, but we are open to other interpretations of that layout.
Preferably, we would like the back side to be clean with just our logo, and the front to contain all of the contact information.

Colors
2f74b4
0355a3
85abd2

Requirements
Must have
• - Logo, company name, needed content - We are open to interpretation beyond that.
• - Standard size business card.
• - Horizontal orientation.
• - Enough space for lengthy names / job titles (for example, a job title could read "Directory of Human Resources" or "V.P. of Governmental Affairs"). We need this to look clean, whether the title be short (CEO) or long (as described above).

```html
<!DOCTYPE html>
<html lang="en">
<head>
<meta charset="UTF-8">
<title>Vantrell Forge Works – Business Card</title>
<link href="https://fonts.googleapis.com/css2?family=Montserrat:wght@400;500;700;800&display=swap" rel="stylesheet">
<style>
  :root {
    --brand-blue: #0e54a2;
    --brand-blue-deep: #0355a3;
    --brand-blue-soft: #85abd2;
    --ink-grey: #6b6e73;
    --rule-grey: #b9bcc0;
    --paper: #ffffff;
    --backdrop: #eef0f3;
  }
  * { box-sizing: border-box; margin: 0; padding: 0; }
  html, body { width: 1200px; height: 800px; overflow: hidden; }
  body {
    background: var(--backdrop);
    font-family: "Montserrat", Arial, sans-serif;
    position: relative;
  }
  .card {
    position: absolute;
    top: 246px;
    width: 540px;
    height: 308px;
    border-radius: 20px;
    box-shadow: 0 6px 18px rgba(0,0,0,0.12);
    overflow: hidden;
  }
  .card-front { left: 40px; background: var(--paper); }
  .card-back  { left: 620px; background: var(--brand-blue); }

  /* Wordmark */
  .wordmark { position: absolute; }
  .wordmark-name {
    font-weight: 800;
    letter-spacing: 1px;
    line-height: 1;
  }
  .wordmark-tagline {
    font-weight: 700;
    letter-spacing: 0.6px;
    text-transform: uppercase;
    margin-top: 8px;
  }
  .card-front .wordmark { left: 34px; top: 110px; }
  .card-front .wordmark-name { font-size: 40px; color: var(--brand-blue); }
  .card-front .wordmark-tagline { font-size: 12.5px; color: var(--ink-grey); }

  .divider {
    position: absolute;
    left: 298px; top: 62px;
    width: 1px; height: 190px;
    background: var(--rule-grey);
  }

  .contact { position: absolute; left: 318px; top: 62px; color: var(--ink-grey); }
  .contact-name { font-size: 17px; font-weight: 700; color: var(--brand-blue); }
  .contact-title { font-size: 11px; margin-top: 4px; }
  .contact-address { font-size: 11px; line-height: 1.55; margin-top: 10px; }
  .contact-lines { list-style: none; margin-top: 6px; }
  .contact-lines li {
    display: flex; align-items: center; gap: 8px;
    font-size: 11.5px; line-height: 1.75;
  }
  .contact-lines svg { width: 12px; height: 12px; fill: var(--brand-blue); flex: none; }

  /* Back */
  .card-back .wordmark { left: 0; right: 0; top: 108px; text-align: center; }
  .card-back .wordmark-name { font-size: 50px; color: var(--paper); }
  .card-back .wordmark-tagline { font-size: 14px; color: var(--paper); }
  .back-web {
    position: absolute; left: 0; right: 0; bottom: 30px;
    text-align: center;
    font-size: 11px;
    color: var(--brand-blue-soft);
  }
</style>
</head>
<body>

<section class="card card-front" aria-label="Business card front">
  <div class="wordmark">
    <div class="wordmark-name">VANTRELL</div>
    <div class="wordmark-tagline">Built for What's Next</div>
  </div>

  <div class="divider"></div>

  <div class="contact">
    <div class="contact-name">Dana Whitlock</div>
    <div class="contact-title">President</div>
    <div class="contact-address">Street Name Avenue, City<br>State, Zip Code, Country</div>
    <ul class="contact-lines">
      <li>
        <svg viewBox="0 0 24 24" aria-hidden="true"><path d="M6.6 10.8a15.1 15.1 0 0 0 6.6 6.6l2.2-2.2a1 1 0 0 1 1-.25 11.4 11.4 0 0 0 3.6.57 1 1 0 0 1 1 1V20a1 1 0 0 1-1 1A17 17 0 0 1 3 4a1 1 0 0 1 1-1h3.5a1 1 0 0 1 1 1c0 1.25.2 2.45.57 3.57a1 1 0 0 1-.25 1z"/></svg>
        +000.000.00 00
      </li>
      <li>
        <svg viewBox="0 0 24 24" aria-hidden="true"><path d="M7 1h10a2 2 0 0 1 2 2v18a2 2 0 0 1-2 2H7a2 2 0 0 1-2-2V3a2 2 0 0 1 2-2zm0 3v14h10V4zm5 15.5a1 1 0 1 0 0 2 1 1 0 0 0 0-2z"/></svg>
        +000.000.00 00
      </li>
      <li>
        <svg viewBox="0 0 24 24" aria-hidden="true"><path d="M6 2h12v5H6zM4 8h16a2 2 0 0 1 2 2v7h-4v5H6v-5H2v-7a2 2 0 0 1 2-2zm4 8v4h8v-4z"/></svg>
        +000.000.00 00
      </li>
      <li>
        <svg viewBox="0 0 24 24" aria-hidden="true"><path d="M2 5h20v14H2zm2 2v.5l8 5 8-5V7zm0 2.9V17h16V9.9l-8 5z"/></svg>
        dana@vantrellforge.com
      </li>
      <li>
        <svg viewBox="0 0 24 24" aria-hidden="true"><path d="M12 2a10 10 0 1 0 0 20 10 10 0 0 0 0-20zm6.9 6h-3a15 15 0 0 0-1.3-3.9A8 8 0 0 1 18.9 8zM12 4c.8 1.1 1.5 2.5 1.9 4h-3.8c.4-1.5 1.1-2.9 1.9-4zM4.3 14a8 8 0 0 1 0-4h3.4a16 16 0 0 0 0 4zm.8 2h3a15 15 0 0 0 1.3 3.9A8 8 0 0 1 5.1 16zm3-8h-3a8 8 0 0 1 4.3-3.9A15 15 0 0 0 8.1 8zM12 20c-.8-1.1-1.5-2.5-1.9-4h3.8c-.4 1.5-1.1 2.9-1.9 4zm2.3-6H9.7a14 14 0 0 1 0-4h4.6a14 14 0 0 1 0 4zm.3 5.9A15 15 0 0 0 15.9 16h3a8 8 0 0 1-4.3 3.9zm1.7-5.9a16 16 0 0 0 0-4h3.4a8 8 0 0 1 0 4z"/></svg>
        www.vantrellforge.com
      </li>
    </ul>
  </div>
</section>

<section class="card card-back" aria-label="Business card back">
  <div class="wordmark">
    <div class="wordmark-name">VANTRELL</div>
    <div class="wordmark-tagline">Built for What's Next</div>
  </div>
  <div class="back-web">www.vantrellforge.com</div>
</section>

</body>
</html>
```